Business Cards for new orthopaedic surgery practice

My husband and I are starting our own orthopaedic surgery practice. We are looking for a business card that is uniform, but one will have my name/title and the other will have his. You can just create one design with my name on it for now. But when I choose your design as the winning design I will ask that you add another copy with his name/title.

We are looking for classy, simple, elite all in one. We like dark blues/a little gold/yellow. Something that goes with our logo. We want our logo incorporated. Here is all the info you need:
Business name: RV Bone & Vitality Center
Location: 38517 North Willowmere Ave
Maple Harbor, FL 33512
Phone: 954-218-4063
Fax: 954-582-7341
Email: info@myrvbonecare.example

Names: Lydia Vance, M.D.
Board Certified Hand and Upper Extremity Surgeon

Ebo Dansu, M.D.
Board Certified Hip & Knee Replacement/General Orthopaedic Surgeon

Can decide what you want to put on the back. Maybe a slogan:
Steady Hands. Strong Recovery

I am just going to upload our logo. The only thing is if we select you as the winning design, the location, and phone numbers may change. We will need your help to update that once fully solidified.

Industry/Entity Type

Medical

Contact Information for Business Card

Colors
0054AA
0677BA
7BADD7
CADEEF
E8F1F8
0094D4
00A9DD
6FCCEA
C7EBF8
E9F6FB

Requirements
Must have
• class, appeal,
Should not have
• We want to air on the side of masculine if we are looking at masculine vs. feminine feel. But we still want it classy, sophisticated, and something we will love

```html
<!DOCTYPE html>
<html lang="en">
<head>
<meta charset="utf-8">
<title>RV Bone &amp; Vitality Center – Business Card</title>
<link href="https://fonts.googleapis.com/css2?family=Arimo:wght@400&family=Libre+Baskerville:wght@700&display=swap" rel="stylesheet">
<style>
  :root{
    --bg:#e4e4e4;
    --navy:#1c2a58;
    --navy-light:#2b3c6e;
    --navy-deep:#18244d;
    --gold:#c9a45c;
    --white:#ffffff;
    --pattern-dark:#1a2650;
    --pattern-light:#34509a;
  }
  html,body{margin:0;padding:0;width:1200px;height:1200px;overflow:hidden;background:var(--bg);}
  .stage{position:relative;width:1200px;height:1200px;}
  .card{position:absolute;width:688px;height:393px;overflow:hidden;}
  .card-front{left:267px;top:159px;background:var(--white);}
  .card-back{left:262px;top:653px;background:var(--navy);}
  .front-shape{position:absolute;inset:0;}
  .doctor-name{position:absolute;left:37px;top:62px;margin:0;font-family:"Libre Baskerville",Georgia,serif;font-weight:700;font-size:22px;letter-spacing:.5px;color:var(--gold);}
  .doctor-title{position:absolute;left:34px;top:91px;margin:0;font-family:"Arimo",Arial,sans-serif;font-size:15.5px;line-height:20px;color:var(--white);}
  .address{position:absolute;left:37px;top:203px;margin:0;font-family:"Arimo",Arial,sans-serif;font-size:16px;line-height:21px;color:var(--white);font-style:normal;}
  .contact-list{position:absolute;left:37px;top:257px;margin:0;padding:0;list-style:none;font-family:"Arimo",Arial,sans-serif;font-size:16px;line-height:20.7px;color:var(--white);}
  .contact-list li{display:flex;align-items:center;gap:11px;}
  .contact-list svg{width:14px;height:14px;flex:none;}
  .brand-mark{position:absolute;left:450px;top:102px;width:190px;height:190px;}
  .brand-mark .ring{position:absolute;inset:0;border:2px solid var(--gold);border-radius:50%;}
  .brand-name{position:absolute;inset:0;display:flex;align-items:center;justify-content:center;text-align:center;margin:0;padding:0 22px;font-family:"Libre Baskerville",Georgia,serif;font-weight:700;font-size:19px;line-height:26px;color:var(--navy);}
  .back-pattern{position:absolute;inset:0;background:linear-gradient(100deg,var(--pattern-dark) 0%,var(--navy-light) 55%,var(--pattern-light) 100%);opacity:.9;}
  .slogan{position:absolute;left:128px;top:294px;margin:0;font-family:"Arimo",Arial,sans-serif;font-size:16px;letter-spacing:3.4px;color:var(--gold);text-transform:uppercase;}
  .back-brand{position:absolute;left:590px;top:286px;width:90px;margin:0;font-family:"Libre Baskerville",Georgia,serif;font-weight:700;font-size:11px;line-height:14px;color:var(--white);}
</style>
</head>
<body>
<main class="stage">
  <section class="card card-front">
    <svg class="front-shape" viewBox="0 0 688 393" aria-hidden="true">
      <defs>
        <linearGradient id="navyFill" x1="0" y1="0" x2="0" y2="1">
          <stop offset="0" stop-color="#2a3a68"/>
          <stop offset="1" stop-color="#1b2754"/>
        </linearGradient>
      </defs>
      <path d="M0 0 H222 C345 30 420 140 396 230 C374 310 318 370 262 393 H0 Z" fill="var(--gold)"/>
      <path d="M0 0 H220 C335 35 400 140 382 225 C362 310 304 365 246 393 H0 Z" fill="var(--white)"/>
      <path d="M0 0 H216 C330 38 394 140 376 225 C356 308 300 362 240 393 H0 Z" fill="url(#navyFill)"/>
    </svg>
    <h1 class="doctor-name">LYDIA VANCE, M.D.</h1>
    <p class="doctor-title">Board Certified Hand and<br>Upper Extremity Surgeon</p>
    <address class="address">38517 North Willowmere Ave<br>Maple Harbor, FL 33512</address>
    <ul class="contact-list">
      <li><svg viewBox="0 0 16 16"><path fill="var(--gold)" d="M3.5 1 6 3.6 4.6 5.5c.8 2 2.2 3.5 4.2 4.5L10.6 8.6 15 11l-1 3c-.3.7-1 1-1.7.8C6.5 13.4 2.5 9.5 1.2 3.6 1 2.9 1.4 2.2 2 2Z"/></svg>954-218-4063</li>
      <li><svg viewBox="0 0 16 16"><path fill="var(--gold)" d="M4 1h8v4H4Z M1 6h14v6h-3v3H4v-3H1Z M5 10v4h6v-4Z"/></svg>954-582-7341</li>
      <li><svg viewBox="0 0 16 16"><path fill="var(--gold)" d="M1 3h14v10H1Z M2 4l6 5 6-5v1L8 10 2 5Z" fill-rule="evenodd"/></svg>info@myrvbonecare.example</li>
      <li><svg viewBox="0 0 16 16"><circle cx="8" cy="8" r="7" fill="var(--gold)"/><path d="M5 4c2 1 1 3 3 3s1 3 3 4M9 2c-1 2 2 2 4 3" stroke="var(--navy)" stroke-width="1.3" fill="none"/></svg>www.myrvbonecare.example</li>
    </ul>
    <div class="brand-mark">
      <span class="ring"></span>
      <p class="brand-name">RV Bone &amp; Vitality Center</p>
    </div>
  </section>

  <section class="card card-back">
    <div class="back-pattern" role="img" aria-label="Repeating embossed pattern of the practice emblem"></div>
    <p class="slogan">Steady hands. Strong recovery</p>
    <p class="back-brand">RV Bone &amp; Vitality Center</p>
  </section>
</main>
</body>
</html>
```